Interior Design/ New Construction interior finishes

Interior Design Website

Target Market(s)

Home builders, New Construction, Renovations, Public

Industry/Entity Type

Construction

Coding

Coded - Design and coding required

Number of Pages Required

1 page

Font styles to use
Sans Serif

Colors

Designer to choose colors to be used in the design.

Requirements
Must have
• Section to upload pictures of projects
• Simple and modern design
• Designer 1 details about myself
• Logo
• Upload section for photos for future jobs
Nice to have
• Sections they can click on to see certain rooms in a house
• Decorating, floral arrangements, holiday decorating.
• I have lots of before and after as well. Maybe a section for those.

```html
<!DOCTYPE html>
<html lang="en">
<head>
<meta charset="utf-8">
<title>Lorna Vale Designs – Interior business &amp; new construction company</title>
<link rel="stylesheet" href="https://fonts.googleapis.com/css2?family=Jost:wght@400;500;600;700&family=PT+Sans:ital,wght@0,400;0,700;1,400&display=swap">
<style>
:root{
  --ink:#1d1d1d;
  --dark:#2f2f2f;
  --panel:#111;
  --grey:#8a8a8a;
  --light:#eeeeee;
  --white:#fff;
  --text:#3a3a3a;
}
*{box-sizing:border-box;margin:0;padding:0}
html,body{width:1200px;height:3352px;overflow:hidden;background:var(--white)}
body{position:relative;font-family:"PT Sans",sans-serif;color:var(--text)}
.abs{position:absolute}
h1,h2,h3,.nav a,.btn{font-family:"Jost",sans-serif}

/* nav */
.topbar{left:0;top:0;width:1200px;height:123px;background:var(--white);border-top:4px solid var(--ink)}
.nav a{position:absolute;top:54px;font-size:16px;font-weight:500;color:var(--ink);text-decoration:none;letter-spacing:.3px}
.logo-disc{left:484px;top:-26px;width:232px;height:232px;border-radius:50%;background:var(--white);z-index:3;display:flex;flex-direction:column;align-items:center;justify-content:center;padding-top:24px}
.logo-dot{width:46px;height:46px;border:3px solid var(--ink);border-radius:50%;margin-bottom:10px}
.logo-name{font-family:"Jost",sans-serif;font-size:21px;font-weight:500;color:var(--ink);letter-spacing:1.5px;text-align:center;line-height:1.15}

/* hero */
.hero{left:0;top:123px;width:1200px;height:514px;background:linear-gradient(180deg,#56514c 0%,#6b655f 45%,#3d3935 100%)}
.hero-title{left:0;top:278px;width:1200px;text-align:center;font-size:82px;font-weight:500;letter-spacing:7px;color:var(--white)}
.hero-sub{left:0;top:398px;width:1200px;text-align:center;font-family:"Jost",sans-serif;font-size:29px;color:var(--white)}
.thumb{border-radius:50%;border:4px solid var(--white);z-index:2}

/* about */
.about-box{left:98px;top:769px;width:405px;height:335px;background:var(--dark)}
.vlabel{font-family:"Jost",sans-serif;font-weight:500;color:var(--white);font-size:28px;letter-spacing:1px;white-space:nowrap;transform:rotate(-90deg);transform-origin:center}
.frame{border:2px solid var(--white);outline:2px solid var(--ink);outline-offset:0}
.photo{position:absolute;inset:6px}
h2.sec{font-size:29px;font-weight:500;color:#555;letter-spacing:.5px}
h2.sec b{font-weight:600;color:var(--ink)}
.rule{height:2px;background:var(--ink)}
.about-text{left:644px;top:852px;width:460px;font-size:15px;line-height:23px;color:#555}
.about-text p+p{margin-top:10px}
.btn{display:flex;align-items:center;justify-content:center;font-weight:600;font-size:15px;color:var(--ink);border:2px solid var(--ink);letter-spacing:.5px}

/* services */
.service{top:1211px;width:400px;height:336px;color:var(--white)}
.service h3{position:absolute;top:160px;font-size:26px;font-weight:600;letter-spacing:.5px}
.service p{position:absolute;top:210px;font-size:15px;line-height:22px;font-weight:700}
.service svg{position:absolute;top:60px}

/* before after */
.arrows{left:531px;top:1893px;width:138px;height:58px;border-radius:29px;overflow:hidden;display:flex;z-index:3}
.arrows span{flex:1;display:flex;align-items:center;justify-content:center}

/* testimonials */
.testi{left:0;top:2193px;width:1200px;height:538px;background:var(--light)}
.quote-text{left:120px;top:2500px;width:960px;text-align:center;font-style:italic;font-size:17.5px;line-height:30px;color:#333}
.dot{width:16px;height:16px;border-radius:50%;border:1.5px solid #333;top:2638px}

/* contact */
.contact{left:0;top:2731px;width:1200px;height:546px;background:linear-gradient(180deg,#3a3835,#25231f 60%,#2e2b27)}
.form{left:635px;top:2834px;width:413px;height:342px;background:var(--panel)}
.field{position:absolute;left:27px;width:337px;border-bottom:2px solid var(--white);color:var(--white);font-family:"Jost",sans-serif;font-size:16px;font-weight:500;padding-bottom:6px}
.send{background:var(--white);border:none;font-size:14px;font-weight:500}

footer{left:0;top:3277px;width:1200px;height:75px;display:flex;align-items:center;justify-content:center;font-family:"Jost",sans-serif;font-weight:500;font-size:16px;color:var(--ink)}
</style>
</head>
<body>

<header class="abs topbar">
  <nav class="nav">
    <a style="left:99px">HOME</a>
    <a style="left:200px">ABOUT US</a>
    <a style="left:336px">INTERIOR</a>
    <a style="left:760px">CONSTRUCTION</a>
    <a style="left:934px">BLOG</a>
    <a style="left:1033px">CONTACT</a>
  </nav>
</header>
<div class="abs logo-disc">
  <span class="logo-dot"></span>
  <span class="logo-name">Lorna Vale<br>Designs</span>
</div>

<section class="abs hero" role="img" aria-label="Bright living room with white armchairs, a wooden coffee table and a tall mirror, under a dark overlay"></section>
<h1 class="abs hero-title">LORNA VALE DESIGNS</h1>
<p class="abs hero-sub">Interior business &amp; new construction company</p>
<div class="abs thumb" style="left:460px;top:599px;width:76px;height:76px;background:#8c7b68" role="img" aria-label="Project thumbnail: living room"></div>
<div class="abs thumb" style="left:556px;top:593px;width:88px;height:88px;background:#4a5058" role="img" aria-label="Project thumbnail: dining area"></div>
<div class="abs thumb" style="left:664px;top:599px;width:76px;height:76px;background:#b8b2aa" role="img" aria-label="Project thumbnail: bright hallway"></div>

<!-- about -->
<div class="abs about-box"></div>
<div class="abs vlabel" style="left:-2px;top:920px;width:290px;text-align:center">INTERIOR BUSINESS</div>
<div class="abs frame" style="left:179px;top:805px;width:412px;height:263px;background:var(--white)">
  <div class="photo" style="background:linear-gradient(90deg,#7a5a44,#c9c2ba 45%,#e6e3df)" role="img" aria-label="Master bathroom with freestanding tub and wooden vanity"></div>
</div>
<h2 class="abs sec" style="left:644px;top:776px">ABOUT <b>LORNA VALE DESIGNS</b></h2>
<div class="abs rule" style="left:644px;top:826px;width:127px"></div>
<div class="abs about-text">
  <p>Nemo enim ipsam voluptatem quia voluptas sit aspernatur aut odit aut fugit, sed quia consequuntur magni dolores eos qui ratione voluptatem sequi nesciunt. Neque porro quisquam est, qui dolorem ipsum quia dolor sit amet, consectetur, adipisci velit, sed quia non numquam eius modi tempora.</p>
  <p>Neque porro quisquam est, qui dolorem ipsum quia dolor sit amet, consectetur, adipisci velit, sed quia non numquam eius modi tempora.</p>
</div>
<a class="abs btn" style="left:644px;top:1046px;width:112px;height:49px">READ MORE</a>

<!-- services -->
<section class="abs service" style="left:0;background:linear-gradient(135deg,#6b5d52,#4a423c)" role="img" aria-label="Decorated bedroom with coffered ceiling">
  <svg style="left:278px" width="70" height="80" viewBox="0 0 70 80" fill="none" stroke="#fff" stroke-width="3"><path d="M35 14c-14 0-18 12-18 26v14l-8 10h52l-8-10V40c0-14-4-26-18-26z"/><circle cx="35" cy="70" r="5"/><path d="M35 14V6M22 4l13 8 13-8"/></svg>
  <h3 style="right:51px">DECORATING</h3>
  <p style="right:51px;width:300px;text-align:right">Sed ut perspiciatis unde omnis iste natus error sit voluptatem accusan tium dolorem quelau dantium</p>
</section>
<section class="abs service" style="left:400px;background:linear-gradient(135deg,#1d1d1d,#2a2a2a)" role="img" aria-label="Dark dining room with pendant lights">
  <svg style="left:165px" width="72" height="72" viewBox="0 0 72 72" fill="none" stroke="#fff" stroke-width="3"><circle cx="36" cy="36" r="9"/><circle cx="36" cy="16" r="10"/><circle cx="36" cy="56" r="10"/><circle cx="16" cy="36" r="10"/><circle cx="56" cy="36" r="10"/><circle cx="22" cy="22" r="10"/><circle cx="50" cy="22" r="10"/><circle cx="22" cy="50" r="10"/><circle cx="50" cy="50" r="10"/></svg>
  <h3 style="left:0;width:400px;text-align:center">FLORAL ARRANGEMENTS</h3>
  <p style="left:50px;width:300px;text-align:right">Sed ut perspiciatis unde omnis iste natus error sit voluptatem accusan tium dolorem quelau dantium</p>
</section>
<section class="abs service" style="left:800px;background:linear-gradient(135deg,#7c6a5c,#a9998a 60%,#8a7b6d)" role="img" aria-label="Foyer with curved staircase and stone floor">
  <svg style="left:282px;top:52px" width="60" height="82" viewBox="0 0 60 82"><rect x="24" y="4" width="12" height="10" fill="#fff"/><circle cx="30" cy="50" r="28" fill="#fff"/><path d="M30 34l4 12 12 4-12 4-4 12-4-12-12-4 12-4z" fill="#8a7b6d"/></svg>
  <h3 style="right:56px">HOLIDAY DECORATING</h3>
  <p style="right:56px;width:300px;text-align:right">Sed ut perspiciatis unde omnis iste natus error sit voluptatem accusan tium dolorem quelau dantium</p>
</section>

<!-- before & after -->
<h2 class="abs sec" style="left:0;top:1628px;width:1200px;text-align:center">BEFORE &amp; <b>AFTER</b></h2>
<div class="abs rule" style="left:537px;top:1680px;width:126px"></div>
<div class="abs" style="left:98px;top:1754px;width:467px;height:336px;background:var(--dark)"></div>
<div class="abs" style="left:697px;top:1754px;width:403px;height:336px;background:var(--grey)"></div>
<div class="abs vlabel" style="left:40px;top:1904px;width:200px;text-align:center">BEFORE</div>
<div class="abs vlabel" style="left:957px;top:1904px;width:200px;text-align:center">AFTER</div>
<div class="abs frame" style="left:179px;top:1790px;width:412px;height:262px;background:var(--white)">
  <div class="photo" style="background:linear-gradient(180deg,#e4e4e4,#cfcfcf 60%,#9a9a9a)" role="img" aria-label="Before: plain room with grey sofa and rug"></div>
</div>
<div class="abs frame" style="left:610px;top:1790px;width:412px;height:262px;background:var(--white)">
  <div class="photo" style="background:linear-gradient(180deg,#8b8782,#77726b 60%,#5d5a55)" role="img" aria-label="After: styled room with yellow sofa, teal armchair and chandelier"></div>
</div>
<div class="abs arrows">
  <span style="background:#2a2a2a"><svg width="20" height="28" viewBox="0 0 20 28" fill="none" stroke="#fff" stroke-width="3"><path d="M15 3L5 14l10 11"/></svg></span>
  <span style="background:#707070"><svg width="20" height="28" viewBox="0 0 20 28" fill="none" stroke="#fff" stroke-width="3"><path d="M5 3l10 11L5 25"/></svg></span>
</div>

<!-- testimonials -->
<section class="abs testi"></section>
<h2 class="abs sec" style="left:0;top:2255px;width:1200px;text-align:center">OUR <b>TESTIMONIALS</b></h2>
<div class="abs rule" style="left:537px;top:2306px;width:126px"></div>
<div class="abs" style="left:546px;top:2369px;width:108px;height:108px;border-radius:50%;background:var(--dark);display:flex;align-items:center;justify-content:center">
  <svg width="48" height="40" viewBox="0 0 48 40" fill="#fff"><path d="M4 40V22C4 10 10 3 20 0l2 5c-6 2-9 6-9 12h8v23zM28 40V22c0-12 6-19 16-22l2 5c-6 2-9 6-9 12h8v23z"/></svg>
</div>
<p class="abs quote-text">Sed ut perspiciatis unde omnis iste natus error sit voluptatem accusantium doloremque laudantium, totam rem aperiam, eaque ipsa quae ab illo inventore veritatis et quasi architecto beatae vitae dicta sunt explicabo.</p>
<p class="abs" style="left:0;top:2578px;width:1200px;text-align:center;font-size:17px;color:#333">- Ellen Marsh</p>
<span class="abs dot" style="left:551px;background:#333"></span>
<span class="abs dot" style="left:571px"></span>
<span class="abs dot" style="left:591px"></span>
<span class="abs dot" style="left:611px"></span>
<span class="abs dot" style="left:631px"></span>

<!-- contact -->
<section class="abs contact" role="img" aria-label="Dim bathroom with marble counters and wood cabinets"></section>
<div class="abs" style="left:221px;top:2834px;width:414px;height:342px;background:linear-gradient(135deg,#8f7a69,#c4b4a4 50%,#a39383)" role="img" aria-label="Bedroom with upholstered headboard and bench"></div>
<form class="abs form">
  <span class="field" style="top:22px">Name *</span>
  <span class="field" style="top:73px">Email *</span>
  <span class="field" style="top:125px">Subject</span>
  <span class="field" style="top:177px;height:49px">Message</span>
  <span class="abs btn send" style="left:27px;top:259px;width:98px;height:43px">SEND NOW</span>
</form>

<footer class="abs">Copyrights @ 2018 Lorna Vale Designs. All Rights Reserved.</footer>
</body>
</html>
```